Modern design company business card design

We are a design oriented construction firm. The owner is an architect and licensed General Contractor and accomplished furniture designer. We do new home construction and large scale remodeling and office design. We would like a design for our new business cards that is clean and modern, but relatable. We like the bright green color of our logo mixed with different shades of grey. We're also open to reinterpreting the logo.

Target Market(s)

Potential design clients,
Construction clients

Industry/Entity Type

Architecture

Contact Information for Business Card

Tall Maple Design | Build Inc. (optional with logo, Inc. optional)Jeffrey MorganOwner (optional)317.555.0148 cell317.431.8056 officejmorgan@greensquareinc.comwww.greensquareinc.com

Font styles to use
Sans Serif
Other font styles liked:
• Avenir

Requirements
Nice to have
• I like designs that have some continuity between the front and back, i.e. similar layouts or graphic elements that wrap around the card. I tend to prefer horizontal over vertical, but that's not a have to. I also tend to prefer white or recycled paper.

```html
<!DOCTYPE html>
<html lang="en">
<head>
<meta charset="utf-8">
<title>Tall Maple Design | Build — Business Card</title>
<link rel="stylesheet" href="https://fonts.googleapis.com/css2?family=Nunito+Sans:wght@300;400;600;800&display=swap">
<style>
  :root {
    --bg: #e8e7e4;
    --paper: #ffffff;
    --green-light: #c3df73;
    --green: #6cbb45;
    --green-deep: #2f8f2c;
    --grey-band: #5b5c60;
    --grey-text: #8f9093;
    --grey-dark: #4a4b4e;
    --shadow: rgba(0,0,0,0.18);
  }
  * { box-sizing: border-box; margin: 0; padding: 0; }
  html, body { width: 1200px; height: 913px; overflow: hidden; }
  body {
    background: var(--bg);
    font-family: "Nunito Sans", "Helvetica Neue", Arial, sans-serif;
    position: relative;
  }
  .card {
    position: absolute;
    width: 520px;
    height: 297px;
    background: var(--paper);
    box-shadow: 0 8px 24px var(--shadow);
    overflow: hidden;
  }
  .card--front { left: 50px; top: 308px; }
  .card--back  { left: 630px; top: 308px; }

  .wordmark {
    color: var(--grey-text);
    font-weight: 300;
    text-transform: uppercase;
    white-space: nowrap;
    line-height: 1;
  }

  /* Front */
  .front__panel {
    position: absolute; left: 0; top: 0; bottom: 0; width: 205px;
    background: linear-gradient(150deg, var(--green-light) 0%, var(--green) 50%, var(--green-deep) 100%);
  }
  .front__band {
    position: absolute; left: 205px; right: 0; bottom: 0; height: 44px;
    background: var(--grey-band);
  }
  .front__wordmark {
    position: absolute; right: 20px; top: 30px;
    font-size: 16px; letter-spacing: 1.5px;
  }
  .front__tab {
    position: absolute; right: 0; top: 76px; width: 30px; height: 22px;
    background: var(--green);
  }
  .person {
    position: absolute; right: 36px; top: 78px; text-align: right;
  }
  .person__name { font-size: 17px; font-weight: 800; color: var(--grey-dark); letter-spacing: 0.5px; text-transform: uppercase; }
  .person__role { font-size: 11px; color: var(--green); letter-spacing: 1px; text-transform: uppercase; margin-top: 1px; }
  .contacts {
    position: absolute; right: 18px; top: 138px; list-style: none;
    font-size: 12.5px; color: var(--grey-dark); text-align: right; line-height: 19px;
  }
  .contacts li { display: flex; justify-content: flex-end; align-items: center; gap: 6px; }
  .contacts svg { width: 11px; height: 11px; flex: none; }

  /* Back */
  .back__wordmark {
    position: absolute; left: 0; right: 0; top: 138px;
    text-align: center;
    font-size: 21px; letter-spacing: 2px;
  }
</style>
</head>
<body>

<section class="card card--front" aria-label="Business card front">
  <div class="front__panel"></div>
  <div class="front__band"></div>
  <div class="wordmark front__wordmark">Tall Maple Design | Build</div>
  <div class="front__tab"></div>
  <div class="person">
    <div class="person__name">Dennis Holloway</div>
    <div class="person__role">Owner</div>
  </div>
  <ul class="contacts">
    <li>317.555.0172
      <svg viewBox="0 0 12 12" fill="none" stroke="var(--green)" stroke-width="1.4"><rect x="3" y="1" width="6" height="10" rx="1"/></svg>
    </li>
    <li>317.555.0148
      <svg viewBox="0 0 12 12" fill="var(--green)"><path d="M2.5 1h2l1 3-1.3 1a6 6 0 0 0 2.8 2.8L8 6.5l3 1v2A1.5 1.5 0 0 1 9.5 11 8.5 8.5 0 0 1 1 2.5 1.5 1.5 0 0 1 2.5 1z"/></svg>
    </li>
    <li>www.tallmapleinc.example
      <svg viewBox="0 0 12 12" fill="none" stroke="var(--green)" stroke-width="1.2"><circle cx="6" cy="6" r="5"/><ellipse cx="6" cy="6" rx="2.2" ry="5"/><path d="M1 6h10"/></svg>
    </li>
    <li>dholloway@tallmapleinc.example
      <svg viewBox="0 0 12 12" fill="none" stroke="var(--green)" stroke-width="1.3"><rect x="1" y="2.5" width="10" height="7"/><path d="M1 2.5l5 4 5-4"/></svg>
    </li>
  </ul>
</section>

<section class="card card--back" aria-label="Business card back">
  <div class="wordmark back__wordmark">Tall Maple Design | Build</div>
</section>

</body>
</html>
```